I require my existing website to be updated

I have an existing website on Squarespace. I would like to refresh it, change some of the copy, add in my new video that we created. I want to give it a new look. My branding is all about geese flying in the V formation, and how that plays out in business when we align our people to our purpose. I have used Pick-Pick-Pebble in the previous site, and now want The Rolling Arc @ Office to replace that narrative. The website is colourful, fun, but needs to have a professional look and I am also looking for more audience engagement on the site. I would like to highlight to a professional small to medium size business audience. I would like to highlight my Brookcast, showcase my speaking, and really utilize the metaphor to put me in a category of one in the speaking and consulting world. My present website is www.meridanpathways.ca

Since the website is on Squarespace, does it need to be coded?

To be clear, I already have a site on Squarespace, I do not need a new site. For those interested in the project, can we make the changes to my existing site, instead of creating and hosting a new one????

I have a new video which I will be uploading.
Updates

Here is the link to the video that I need on my website https://qx.example/Tr83mPzd

Target Market(s)

Small to medium size businesses -

Industry/Entity Type

Business Consulting, Coaching, Speaking

Number of Pages Required

5+ page

Font styles to use
Other font styles liked:
• Calibri, Marydale, Futura

Requirements
Must have
• Color, fun, and showcase The Rolling Arc @ Office. It must have my video, Brookcast, and a place for people to want to engage. My case study and e-book to download. Logo's of companies that I have worked with
Nice to have
• A place for people to engage with the site. Testimonials from clients. Copy or video.
Should not have
• A traditional or boring look

```html
<!DOCTYPE html>
<html lang="en">
<head>
<meta charset="utf-8">
<title>Meridan Pathways</title>
<link rel="stylesheet" href="https://fonts.googleapis.com/css2?family=Gochi+Hand&family=Carlito:wght@400;700&display=swap">
<style>
:root{
  --blue:#3fa9d4;
  --blue-deep:#2b8fbd;
  --band:#5aa9cc;
  --yellow:#ffc20e;
  --ink:#222;
  --muted:#555;
  --pale:#eef6fb;
  --white:#fff;
}
*{box-sizing:border-box;margin:0;padding:0}
html,body{width:1200px;height:4458px;overflow:hidden}
body{position:relative;background:var(--white);font-family:"Carlito",Calibri,Arial,sans-serif;color:var(--ink)}
.abs{position:absolute}
.hand{font-family:"Gochi Hand",cursive;font-weight:400}
.btn{position:absolute;background:var(--yellow);color:var(--white);font-family:"Gochi Hand",cursive;font-size:18px;display:flex;align-items:center;justify-content:center;border-radius:3px}
.section-title{position:absolute;left:0;width:1200px;text-align:center;font-family:"Gochi Hand",cursive;color:var(--blue);font-size:34px;text-transform:uppercase}
.photo{position:absolute}

/* header */
.site-header{position:absolute;left:0;top:0;width:1200px;height:105px;background:var(--white)}
.brand{position:absolute;left:105px;top:20px;display:flex;align-items:center;gap:14px}
.brand-dot{width:68px;height:68px;border-radius:50%;background:#111}
.brand-name{font-size:24px;font-weight:700;letter-spacing:4px;line-height:1}
.brand-name small{display:block;font-size:13px;font-weight:400;letter-spacing:6px;margin-top:4px}
.socials{position:absolute;display:flex;gap:22px}
.socials span{width:26px;height:26px;border-radius:50%;display:block}
.s1{background:#d6307a}.s2{background:#1877f2}.s3{background:#1da1f2}.s4{background:#e62117}
.main-nav{position:absolute;left:505px;top:66px;display:flex;gap:30px;font-size:14px;color:#333}
.main-nav .active{color:var(--blue);font-weight:700;border-bottom:2px solid var(--blue);padding-bottom:6px}

/* hero */
.hero-photo{left:0;top:105px;width:1200px;height:660px;background:linear-gradient(180deg,#4f5f73 0%,#7d8795 35%,#c9a47a 62%,#f2a43c 72%,#3a2c26 85%,#1d1a1c 100%)}
.hero-welcome{left:700px;top:318px;width:400px;text-align:right;color:var(--white);font-size:32px}
.hero-title{left:600px;top:360px;width:500px;text-align:right;color:var(--white);font-size:58px;line-height:1}

/* brookcast */
.pod-title{left:104px;top:878px;color:var(--blue);font-size:36px}
.pod-copy{left:104px;top:928px;width:460px;font-size:15.5px;line-height:26px;color:var(--ink)}
.pod-copy p+p{margin-top:12px}

/* case study */
.case-band{left:0;top:1315px;width:1200px;height:750px;background:linear-gradient(180deg,#5ba6c8,#4fa8d0)}
.card{position:absolute;top:1500px;width:308px;height:430px;background:var(--white);border-radius:10px;padding:6px}
.card-photo{width:296px;height:190px;border-radius:10px}
.card h3{font-family:"Gochi Hand",cursive;font-weight:400;color:var(--blue);text-align:center;font-size:22px;margin-top:24px}
.card p{text-align:center;font-size:13.5px;line-height:22px;color:#444;padding:8px 18px 0}
.card .btn{left:92px;top:362px;width:124px;height:40px}

/* ebook */
.ebook-blob{left:120px;top:2156px;width:340px;height:420px}
.ebook-title{left:564px;top:2200px;color:var(--blue);font-size:32px}
.ebook-copy{left:564px;top:2254px;width:520px;font-size:15px;line-height:26px}
.ebook-copy strong{font-size:17px}

/* clients */
.pale-bg{left:0;top:2660px;width:1200px;height:1798px;background:linear-gradient(180deg,var(--pale),#f7fbfd 60%,#eaf4f9)}
.client{position:absolute;top:2905px;width:236px;height:80px;background:var(--white);display:flex;align-items:center;justify-content:center;gap:8px;font-size:19px;font-weight:700;color:#222;box-shadow:0 1px 4px rgba(0,0,0,.06)}
.client i{width:16px;height:16px;background:#222;display:block;border-radius:50%}

/* testimonial */
.t-name{left:570px;top:3346px;color:var(--blue);font-size:26px}
.t-sub{left:570px;top:3390px;font-size:17px}
.t-stars{left:570px;top:3422px;color:var(--yellow);font-size:18px;letter-spacing:2px}
.t-copy{left:570px;top:3460px;width:520px;font-size:16px;line-height:26.5px}

/* newsletter */
.field{position:absolute;top:4000px;height:46px;background:var(--white);border:1px solid #d8e2e8;font-size:16px;color:#6a8fb0;padding:12px 26px}
.rule{left:104px;top:4088px;width:992px;height:1px;background:#cfdde6}
.foot-brand{left:0;top:4110px;width:1200px;display:flex;flex-direction:column;align-items:center;gap:10px}
.foot-brand .brand-dot{width:124px;height:124px}
.foot-brand .brand-name{text-align:center;font-size:16px}
.foot-brand .brand-name small{font-size:10px}
.foot-nav{left:0;top:4316px;width:1200px;text-align:center;font-size:15px;word-spacing:2px}
.foot-nav span{margin:0 14px}
.copyright{left:0;top:4392px;width:1200px;text-align:center;font-size:15px}
</style>
</head>
<body>

<header class="site-header">
  <div class="brand"><span class="brand-dot"></span><div class="brand-name">MERIDAN<small>PATHWAYS</small></div></div>
  <div class="socials" style="left:920px;top:24px"><span class="s1"></span><span class="s2"></span><span class="s3"></span><span class="s4"></span></div>
  <nav class="main-nav"><span class="active">Home</span><span>Who We Are</span><span>What We Do</span><span>Who We Help</span><span>Media E Book</span><span># Betterthebrook</span></nav>
</header>

<div class="photo hero-photo" role="img" aria-label="Geese flying in a V over a sunset lake"></div>
<svg class="abs" style="left:0;top:640px" width="1200" height="140" viewBox="0 0 1200 140">
  <path d="M0 70 C200 20 420 40 640 75 C850 105 1000 70 1200 40 L1200 140 L0 140Z" fill="var(--blue)"/>
  <path d="M0 90 C220 40 430 55 640 88 C850 120 1020 90 1200 75 L1200 140 L0 140Z" fill="var(--white)"/>
</svg>
<div class="abs hand hero-welcome">Welcome To</div>
<div class="abs hand hero-title">Meridan Pathways</div>
<div class="btn" style="left:982px;top:506px;width:124px;height:44px">Get Started</div>

<h2 class="abs hand pod-title">BROOKCAST</h2>
<div class="abs pod-copy">
  <p>Do you ever feel like you're dancing to the beat of a different drum? A goose in the midst of a pond full of ducks? We are all uniquely different. There can be incredible success when we are allowed to function in our unique skill sets for our personal lives, and also for the organizations we serve.</p>
  <p>It's time to give yourself permission to be you - flaws and all. It's that simple. You matter. You make a difference. You're awesome.</p>
</div>
<div class="btn" style="left:104px;top:1140px;width:124px;height:44px">Watch Now</div>
<svg class="abs" style="left:660px;top:835px" width="420" height="420" viewBox="0 0 420 420">
  <circle cx="210" cy="210" r="200" fill="none" stroke="var(--yellow)" stroke-width="3"/>
  <circle cx="144" cy="16" r="12" fill="var(--yellow)"/>
  <circle cx="212" cy="214" r="178" fill="#8d9aa3"/>
  <circle cx="212" cy="214" r="36" fill="var(--blue)" opacity=".85"/>
  <path d="M202 198 L228 214 L202 230Z" fill="var(--white)"/>
</svg>

<div class="abs case-band" role="img" aria-label="Faded blue backdrop of geese in flight"></div>
<h2 class="section-title" style="top:1408px;color:var(--white)">Case Study</h2>
<article class="card" style="left:104px">
  <div class="card-photo" role="img" aria-label="Goose close-up among ducks" style="background:linear-gradient(135deg,#9c8a78,#5f6f5c)"></div>
  <h3>GOOSE - INDIVIDUALS</h3>
  <p>Do you feel like a misfit? Feel like you aren't contributing to your full potential? That you are flying outside the "V" and bucking a headwind feeling tired and frustrated?</p>
  <div class="btn">Read More</div>
</article>
<article class="card" style="left:446px">
  <div class="card-photo" role="img" aria-label="Flock of white geese walking together" style="background:linear-gradient(135deg,#c9c4bc,#6f6a66)"></div>
  <h3>FLOCK - TEAMS</h3>
  <p>Every organization has teams of people that work together to contribute to the whole. Each team is dynamic, and has its own goals of what needs to be accomplished.</p>
  <div class="btn">Read More</div>
</article>
<article class="card" style="left:787px">
  <div class="card-photo" role="img" aria-label="Calm pond with ripples at sunset" style="background:linear-gradient(180deg,#e9a45a,#7d6a66 60%,#3b4350)"></div>
  <h3>POND - ORGANIZATIONS</h3>
  <p>Are you the leader of the organization? You are responsible for the individual geese, the flocks, and the entire pond. You see the pond differently.</p>
  <div class="btn">Read More</div>
</article>

<div class="abs ebook-blob" role="img" aria-label="E-book cover on a tablet" style="border-radius:48% 52% 45% 55%/50% 40% 60% 50%;background:radial-gradient(circle at 50% 50%,#2a2a2a 0 45%,#e6e8ea 46%)"></div>
<h2 class="abs hand ebook-title">E - Book</h2>
<div class="abs ebook-copy">
  <strong>Move From Transition To Your Truest Self.</strong><br>
  An Ebook By Dale Corwin.<br>
  <strong>What Is Being In Transition?</strong><br>
  In My World, We Use A Tool Called The Strata Drive Index.<br>
  The Strata Drive Index Is A Tool I Use To Help People Discover Their Innate And Instinctive Strengths. It Measures Your Problem-solving Center Or The Conative Aspect Of The Mind. This Part Of Your Mind Does Not Change Over Time. It Is The Part Of You That You Can Count On When You Have The Freedom To Be Yourself.
</div>
<div class="btn" style="left:560px;top:2514px;width:126px;height:42px">Download Now</div>

<div class="abs pale-bg"></div>
<svg class="abs" style="left:0;top:2640px" width="1200" height="60" viewBox="0 0 1200 60"><path d="M0 0 H1200 V20 C1000 50 800 10 600 30 C400 50 200 15 0 30Z" fill="var(--white)"/></svg>
<h2 class="section-title" style="top:2815px">Our Clients</h2>
<div class="client" style="left:104px">Ashgrove &amp; Lane</div>
<div class="client" style="left:354px"><i></i>Kestrel Medics</div>
<div class="client" style="left:610px">Clearview Aesthetics</div>
<div class="client" style="left:860px"><i></i>Harlow Brokers</div>

<h2 class="section-title" style="top:3212px">What Our Clients Say</h2>
<svg class="abs" style="left:120px;top:3310px" width="410" height="400" viewBox="0 0 410 400">
  <path d="M40 70 C120 -10 320 0 380 120 C420 230 340 380 200 390 C60 395 0 260 10 170 C15 120 25 90 40 70Z" fill="none" stroke="var(--yellow)" stroke-width="3"/>
  <path d="M55 85 C130 15 310 20 365 125 C400 230 330 370 200 375 C75 378 20 255 28 170 C32 125 42 100 55 85Z" fill="#9aa4ac"/>
  <circle cx="190" cy="220" r="32" fill="var(--blue)" opacity=".85"/>
  <path d="M181 205 L204 220 L181 235Z" fill="var(--white)"/>
</svg>
<div class="abs hand t-name">Reid Tamsin</div>
<div class="abs t-sub">–&nbsp; Lorem ipsum dolor</div>
<div class="abs t-stars">★★★★★</div>
<p class="abs t-copy">Lorem ipsum dolor sit amet, consectetur adipiscing elit, sed do eiusmod tempor incididunt ut labore et dolore magna aliqua. Ut enim ad minim veniam, quis nostrud exercitation ullamco laboris nisi ut aliquip ex ea commodo consequat. Duis aute irure dolor in reprehenderit in voluptate velit esse cillum dolore eu fugiat nulla pariatur. Lorem ipsum dolor sit amet, consectetur adipiscing elit, sed do eiusmod tempor incididunt ut labore et dolore magna aliqua.</p>
<svg class="abs" style="left:574px;top:3688px" width="44" height="20" viewBox="0 0 44 20">
  <circle cx="9" cy="9" r="8" fill="var(--blue)"/><path d="M11 5 L7 9 L11 13" stroke="#fff" stroke-width="2" fill="none"/>
  <circle cx="33" cy="9" r="8" fill="#111"/><path d="M31 5 L35 9 L31 13" stroke="#fff" stroke-width="2" fill="none"/>
</svg>

<svg class="abs" style="left:0;top:3760px" width="1200" height="110" viewBox="0 0 1200 110">
  <path d="M0 48 C250 30 450 95 700 80 C900 68 1050 30 1200 22" stroke="var(--blue)" stroke-width="12" fill="none"/>
  <path d="M0 62 C260 50 460 110 700 95 C900 82 1060 50 1200 40 L1200 110 L0 110Z" fill="#f6fafd"/>
</svg>
<h2 class="section-title" style="top:3910px">Newsletter</h2>
<div class="field" style="left:175px;width:350px">Name</div>
<div class="field" style="left:543px;width:350px">Email Address</div>
<div class="btn" style="left:904px;top:4000px;width:124px;height:44px">Submit</div>
<div class="abs rule"></div>

<div class="abs foot-brand"><span class="brand-dot"></span><div class="brand-name">MERIDAN<small>PATHWAYS</small></div></div>
<nav class="abs foot-nav">Home <span>|</span> Who We Are <span>|</span> What We Do <span>|</span> Who We Help <span>|</span> Media E Book <span>|</span> # Betterthebrook</nav>
<div class="abs copyright">©2023 Meridan Pathways | All Rights Reserved</div>
<div class="socials" style="left:982px;top:4393px;gap:12px"><span class="s2" style="width:20px;height:20px"></span><span class="s1" style="width:20px;height:20px"></span><span class="s3" style="width:20px;height:20px"></span><span class="s4" style="width:20px;height:20px"></span></div>

</body>
</html>
```